Business Card Design

We would like to re-design our business cards. Our Company - Qwinrel Turbochargers, rebuilds turbochargers and sells replacement parts. Our website is: http://www.qwinrelturbochargers-example.com
We just had our logo changed. I will attach the file. Looking for fresh new/modern business card. We like the colors red, black, white and silver. Black background looks attractive, but not a requirement. The final design should communicate reasonable/competitive prices, top quality and reliability of our products.
Updates
Project Deadline Extended
Reason: Need to finalize the info on the card. Currently working on changing address and email info. Want to make sure it is the correct one before accepting the final design. Unless, this is something that can be changed at a later time..??
Industry/Entity Type
Business
Contact Information for Business Card
QWINREL TURBOCHARGERS, LLC
20473 Harwick Lane NE
Massillon, OH 44647
Tel: +1-555-214-7390
Fax: +1-555-267-1842
info@QwinrelTurbochargers-example.com
Our current business card had the following highlights:
*We rebuild all Turbocharges for Automotive, Diesel and Industrial
*Precision Balancing and in-house turbocharger needs
*All Turbocharger replacement parts are made in USA / U.K.
Look and feel
Each slider illustrates characteristics of the customer's brand and the style your logo design should communicate.

```html
<!DOCTYPE html>
<html lang="en">
<head>
<meta charset="utf-8">
<title>Qwinrel Turbochargers – Business Card</title>
<link href="https://fonts.googleapis.com/css2?family=Lato:wght@400;700&display=swap" rel="stylesheet">
<style>
  :root {
    --backdrop: #3a3330;
    --card-black: #161616;
    --card-edge: #0c0c0c;
    --text-white: #f2f2f2;
    --text-soft: #d6d6d6;
    --brand-red: #e3222b;
    --brand-silver: #b9b9b9;
    --divider: rgba(255, 255, 255, 0.08);
  }
  * { box-sizing: border-box; margin: 0; padding: 0; }
  html, body {
    width: 1200px;
    height: 844px;
    overflow: hidden;
    background: var(--backdrop);
    font-family: "Lato", Arial, sans-serif;
  }
  .card-sheet {
    width: 1200px;
    height: 844px;
    display: flex;
    align-items: center;
    justify-content: center;
    gap: 60px;
  }
  .card {
    width: 520px;
    height: 300px;
    background: var(--card-black);
    border: 1px solid var(--card-edge);
    box-shadow: 0 14px 30px rgba(0, 0, 0, 0.45);
    position: relative;
  }
  .card-front { display: flex; }
  .front-brand {
    width: 48%;
    display: flex;
    align-items: center;
    justify-content: center;
    gap: 10px;
  }
  .brand-square {
    width: 22px;
    height: 22px;
    background: var(--brand-red);
    flex: none;
  }
  .brand-name {
    color: var(--text-white);
    font-weight: 700;
    font-size: 17px;
    line-height: 1;
    white-space: nowrap;
  }
  .front-details {
    width: 52%;
    border-left: 1px solid var(--divider);
    padding: 42px 16px 0 24px;
    color: var(--text-soft);
    font-size: 14px;
    line-height: 1.35;
    white-space: nowrap;
  }
  .person-name {
    color: var(--text-white);
    font-size: 21px;
    font-weight: 400;
    line-height: 1.1;
  }
  .person-role {
    font-size: 13px;
    margin-bottom: 18px;
  }
  .address { margin-bottom: 16px; }
  .contact-list { list-style: none; }
  .card-back {
    display: flex;
    align-items: center;
    justify-content: center;
    gap: 12px;
  }
  .card-back .brand-square {
    width: 28px;
    height: 28px;
    background: var(--brand-silver);
  }
  .card-back .brand-name {
    color: var(--brand-silver);
    font-size: 24px;
  }
</style>
</head>
<body>
  <main class="card-sheet">
    <section class="card card-front" aria-label="Card front">
      <div class="front-brand">
        <span class="brand-square"></span>
        <span class="brand-name">Qwinrel Turbochargers</span>
      </div>
      <div class="front-details">
        <h1 class="person-name">Dorian Mellick</h1>
        <p class="person-role">Managing Director</p>
        <p class="address">20473 Harwick Lane NE<br>Massillon, OH 44647</p>
        <ul class="contact-list">
          <li>T: +1-555-214-7390</li>
          <li>E: info@qwinrel-example.com</li>
          <li>W: www.qwinrel-example.com</li>
        </ul>
      </div>
    </section>
    <section class="card card-back" aria-label="Card back">
      <span class="brand-square"></span>
      <span class="brand-name">Qwinrel Turbochargers</span>
    </section>
  </main>
</body>
</html>
```